KLV Plant Services

We are a heavy diesel mechanical business with additional air con certificates, remapping engine rebuilt

Contact Information for Business Card

Company Name, Director Name, Managing Director, Contact details, email and website

Font styles to use
Serif
Script

```html
<!DOCTYPE html>
<html lang="en">
<head>
<meta charset="utf-8">
<title>KLV Plant Services – Business Card</title>
<link rel="stylesheet" href="https://fonts.googleapis.com/css2?family=Saira:wght@700&family=Varela+Round&display=swap">
<style>
  :root {
    --stage: #2b2b2d;
    --card-dark: #2a2a2b;
    --card-dark-edge: #3a3a3b;
    --card-light: #ffffff;
    --navy: #25236b;
    --ink: #2b2b2d;
    --text: #3a3a3e;
    --white: #ffffff;
  }
  * { box-sizing: border-box; margin: 0; padding: 0; }
  html, body {
    width: 1200px; height: 900px; overflow: hidden;
    background: var(--stage);
  }
  .canvas {
    position: relative; width: 1200px; height: 900px;
    display: flex; flex-direction: column; align-items: center;
    justify-content: center; gap: 40px;
  }
  .card {
    position: relative; width: 680px; height: 390px;
    border-radius: 28px; overflow: hidden;
    box-shadow: 0 18px 40px rgba(0,0,0,.45);
  }

  /* Back side */
  .card-back {
    background: linear-gradient(135deg, var(--card-dark-edge) 0%, var(--card-dark) 55%, #1f1f20 100%);
    display: flex; align-items: center; justify-content: center;
  }
  .brand-name {
    font-family: "Saira", sans-serif; font-weight: 700;
    white-space: nowrap; line-height: 1;
  }
  .card-back .brand-name { font-size: 52px; color: var(--white); }

  /* Front side */
  .card-front { background: var(--card-light); }
  .front-brand {
    position: absolute; left: 0; top: 0; width: 330px; height: 350px;
    display: flex; align-items: center; justify-content: center;
  }
  .front-brand .brand-name { font-size: 30px; color: var(--navy); }
  .divider {
    position: absolute; left: 330px; top: 48px; width: 2px; height: 250px;
    background: var(--navy);
  }
  .details {
    position: absolute; left: 362px; top: 50px; right: 24px;
    font-family: "Varela Round", sans-serif; color: var(--text);
  }
  .person-name {
    font-family: "Saira", sans-serif; font-weight: 700;
    font-size: 34px; color: var(--navy); letter-spacing: 1px; line-height: 1;
  }
  .person-role { font-size: 17px; margin-top: 4px; }
  .address { font-size: 17px; line-height: 1.3; margin-top: 14px; }
  .contact-list { list-style: none; margin-top: 14px; }
  .contact-list li {
    display: flex; align-items: center; gap: 10px;
    font-size: 17px; line-height: 1.55;
  }
  .contact-list svg { width: 14px; height: 14px; flex: none; fill: var(--navy); }
  .front-rule {
    position: absolute; left: 0; right: 0; bottom: 38px; height: 2px;
    background: var(--ink);
  }
  .front-band {
    position: absolute; left: 0; right: 0; bottom: 0; height: 30px;
    background: var(--navy);
  }
</style>
</head>
<body>
<main class="canvas">
  <section class="card card-back" aria-label="Business card back">
    <p class="brand-name">KLV Plant Services</p>
  </section>

  <section class="card card-front" aria-label="Business card front">
    <div class="front-brand">
      <p class="brand-name">KLV Plant Services</p>
    </div>
    <div class="divider"></div>
    <div class="details">
      <h1 class="person-name">DANIEL HARROW</h1>
      <p class="person-role">Managing Director</p>
      <p class="address">P.O. Box 418 Harlow Road<br>Westfield AB, T2K 4R7</p>
      <ul class="contact-list">
        <li>
          <svg viewBox="0 0 24 24" aria-hidden="true"><path d="M6.6 10.8a15.1 15.1 0 0 0 6.6 6.6l2.2-2.2a1 1 0 0 1 1-.25 11.4 11.4 0 0 0 3.6.57 1 1 0 0 1 1 1V20a1 1 0 0 1-1 1A17 17 0 0 1 3 4a1 1 0 0 1 1-1h3.5a1 1 0 0 1 1 1c0 1.25.2 2.45.57 3.57a1 1 0 0 1-.25 1z"/></svg>
          555-014-2290
        </li>
        <li>
          <svg viewBox="0 0 24 24" aria-hidden="true"><path d="M2 5h20v14H2zm2 2v.5l8 5 8-5V7zm0 2.9V17h16V9.9l-8 5z"/></svg>
          info@klvplantservices.com
        </li>
        <li>
          <svg viewBox="0 0 24 24" aria-hidden="true"><circle cx="12" cy="12" r="10"/></svg>
          www.klvplantservices.com
        </li>
      </ul>
    </div>
    <div class="front-rule"></div>
    <div class="front-band"></div>
  </section>
</main>
</body>
</html>
```